Im want a website LIKE VRX's and FleetHollow.com's with product payment options like Trenzo's

I need a website LIKE VRX with a header made EXACTLY LIKE THAT OF FLEETHOLLOWS .

The front page photo should be like that of FLEETHOLLOW's webpage as well.

The name of the website will be called "M.K. (Caldera Key)".

We will be targeting ALL MARKETS in a small town in central Panama and charging businesses "listing fees" like a phone book does but also providing informational blogs, news, and other interesting activities.

THIS IS A MULTI PAGE WEBSITE

THIS IS WHERE VRX's website meets Brivelle/FleetHollow.

Once the layout is built I will tweak and modify, add information, and upload items for sale.

Here is a list of specific categories that should be listed out above the front page header image/search bar

-- Home -- News -- Travel -- Activities -- Shop & Dine -- Store -- More... --

These categories should be spread across the bottom of the page in three sections:

WHATS SO GREAT ABOUT (Caldera Key),
HAND PICKED TOURS
ACTIVITIES etc.

Also lets use www.Trenzo.example 's
"HOT DESTINATIONS"
"BEAT THE BEST PRICES IN BOQUETE"
"OCTOBERS INSIDER PICKS"
"TOP DESTINATIONS"
and spread them in four sections side-by-side near the bottom of the page.

Overall I would like to see the finished product to be something LIKE VRX's and FleetHollows.

WE NEED ONLINE PAYMENT OPTIONS LIKE BRIVELLE'S WEBSITE HAS

This will be a desktop website but should be very mobile friendly as well.

-rodmund

P.S. Good luck!

If it isn't already too late to change the website name, the name of the website should be "Caldera Key". Added Friday, October 9, 2015

What do you guys think the budget should be to win this? Added Saturday, October 10, 2015

www.palmorra.example is the most amazing simple site. Whoever can make me a replica with my specifications will win immediately!!!! Added Sunday, October 18, 2015

OMG www.palmorra.example is the bomb!So simple and elegant. Whoever can make me an EXACT REPLICA OF WWW.PALMORRA.EXAMPLE as my site with the specifications mentioned in my brief will take home the $825.00 immediately! Good luck amigos! Added Sunday, October 18, 2015

Does anybody know how to add recurring monthly billing options on this website? Added Sunday, October 18, 2015

ALL MARKETS

Product

Coded - Design and coding required

5+ page

• Coinvey payment options.
• I must be able to add and remove photos/text and video from the HTML files in the page.
• Be creative my friends, and may the odds be forever in your favor!
• I added some photos of a good layout for our page below.

```html
<!DOCTYPE html>
<html lang="en">
<head>
<meta charset="utf-8">
<title>Caldera Key</title>
<link href="https://fonts.googleapis.com/css2?family=Raleway:ital,wght@0,400;0,600;0,700;1,700&family=Open+Sans:wght@400;600&display=swap" rel="stylesheet">
<style>
  :root{
    --teal:#1ba6b8;
    --teal-dark:#14899a;
    --ink:#1c1c1c;
    --bar:#1a1a1a;
    --footer:#141414;
    --grey-text:#666;
    --light:#f2f2f2;
    --star:#f2b01e;
    --white:#fff;
  }
  *{box-sizing:border-box;margin:0;padding:0}
  html,body{width:781px;height:1200px;overflow:hidden}
  body{font-family:"Open Sans",Arial,sans-serif;color:var(--ink);background:var(--white);font-size:9px;line-height:1.4}
  .wrap{width:651px;margin:0 auto;position:relative}

  /* top bar */
  .topbar{height:24px;background:var(--bar);color:var(--white)}
  .topbar .wrap{display:flex;justify-content:space-between;align-items:center;height:24px}
  .currency{font-size:9px;font-weight:600}
  .account{display:flex;gap:6px}
  .account a{display:inline-block;background:var(--teal);color:var(--white);text-decoration:none;font-size:8px;padding:2px 12px;border-radius:2px}
  .account a.register{background:#0d6d7a}

  /* header */
  .site-header{height:76px;background:var(--white)}
  .site-header .wrap{height:76px}
  .brand{position:absolute;left:0;top:16px;font-family:"Raleway",sans-serif;font-weight:700;font-size:26px;color:var(--teal);letter-spacing:.3px}
  .cart{position:absolute;left:478px;top:14px;width:20px;height:20px;border-radius:50%;background:var(--teal)}
  .cart svg{position:absolute;left:4px;top:4px}
  .search-line{position:absolute;left:506px;top:24px;width:145px;height:1px;background:#ccc}
  .main-nav{position:absolute;right:0;top:46px;display:flex;font-family:"Raleway",sans-serif;font-size:9px;font-weight:600}
  .main-nav a{color:var(--ink);text-decoration:none;padding:6px 12px}
  .main-nav a.active{background:var(--teal);color:var(--white)}

  /* hero */
  .hero{position:relative;height:316px;background:linear-gradient(180deg,#8fd0ec 0%,#bfe6f4 28%,#2fc2c9 40%,#1aa7b6 55%,#6fd3cf 70%,#e9e2cf 86%,#f4efe2 100%)}
  .hero-photo{position:absolute;inset:0}
  .hero-title{position:absolute;left:0;right:0;top:150px;text-align:center;font-family:"Raleway",sans-serif;font-weight:700;font-size:22px;color:var(--white);text-shadow:0 1px 3px rgba(0,0,0,.35)}
  .hero-title em{font-style:italic;color:var(--white)}
  .hero-dots{position:absolute;left:0;right:0;top:294px;display:flex;justify-content:center;gap:6px}
  .hero-dots span{width:6px;height:6px;border-radius:50%;background:rgba(255,255,255,.6)}
  .hero-dots span.on{background:var(--white)}

  /* services */
  .services{padding:0 0 0}
  .services .wrap{display:flex;justify-content:space-between}
  .service{width:208px}
  .service-img{height:104px}
  .service h3{font-family:"Raleway",sans-serif;font-size:11px;font-weight:700;color:var(--teal);margin:18px 0 3px}
  .service p{color:var(--grey-text);font-size:7.5px;line-height:1.35}
  .btn{display:inline-block;background:var(--teal);color:var(--white);font-size:7.5px;padding:4px 10px;text-decoration:none;border-radius:2px}
  .service .btn{margin-top:10px}

  /* converter */
  .converter{margin-top:18px;height:143px;position:relative;background:linear-gradient(100deg,#0f3f49 0%,#1b5f66 35%,#0e2f37 70%,#2a5458 100%)}
  .converter .wrap{display:flex;gap:22px;padding-top:13px}
  .converter-box{width:247px;height:122px;background:var(--teal);color:var(--white);padding:6px 12px}
  .converter-box h2{font-family:"Raleway",sans-serif;font-size:12px;font-weight:600;text-align:center;margin-bottom:8px}
  .field{display:flex;align-items:center;margin-bottom:6px;font-size:8px}
  .field label{width:34px}
  .field .select{flex:1;height:14px;background:#0d6e7c;border:1px solid rgba(255,255,255,.35);font-size:7px;padding:1px 5px;display:flex;justify-content:space-between;align-items:center}
  .field .select b{width:8px;height:8px;background:var(--white);display:inline-block}
  .field .input{width:60px;height:14px;background:var(--white)}
  .field .btn-go{margin-left:6px;background:#0d6e7c;padding:2px 8px;font-size:7px}
  .converter-copy{color:var(--white);padding-top:8px;width:370px}
  .converter-copy h2{font-family:"Raleway",sans-serif;font-size:15px;font-weight:400;margin-bottom:6px}
  .converter-copy p{font-size:7.5px;line-height:1.45;color:#dbe8ea}
  .converter-copy .btn{margin-top:10px}

  /* populars */
  .populars{padding-top:14px}
  .populars h2{font-family:"Raleway",sans-serif;font-size:16px;font-weight:400;color:var(--teal);margin-left:-4px;margin-bottom:8px}
  .pop-list{display:flex;justify-content:space-between;padding:0 22px}
  .pop{width:143px;background:var(--light);padding:6px 8px 8px}
  .pop h3{font-family:"Raleway",sans-serif;font-weight:600;font-size:11px;color:var(--teal);margin-bottom:5px}
  .pop-img{height:72px}
  .stars{color:var(--star);font-size:9px;letter-spacing:1px;margin-top:4px}
  .pop p{font-size:7px;color:var(--grey-text);margin:2px 0 4px}
  .pop-foot{display:flex;justify-content:space-between;align-items:center}
  .pop-foot .more{color:var(--teal);font-size:7px}
  .price{font-family:"Raleway",sans-serif;font-size:14px;font-weight:700;color:var(--teal)}
  .pop .btn{margin-top:4px;font-size:7px;padding:3px 8px}
  .pager{display:flex;justify-content:flex-end;gap:3px;margin:10px 0 0}
  .pager span{width:11px;height:11px;background:var(--teal);color:var(--white);font-size:7px;text-align:center;line-height:11px}

  /* footer */
  .site-footer{position:absolute;left:0;right:0;top:1067px;height:133px;background:var(--footer);color:#cfcfcf}
  .footer-cols{display:flex;padding-top:12px}
  .footer-cols h4{font-family:"Raleway",sans-serif;color:var(--white);font-size:11px;font-weight:600;margin-bottom:6px}
  .col-about{width:185px}
  .col-about p{font-size:7px;line-height:1.45}
  .col-about .btn{margin-top:8px}
  .col-links{width:120px}
  .col-links li{list-style:none;font-size:7px;line-height:1.5}
  .col-news{width:220px}
  .news-form{display:flex}
  .news-form span{width:110px;height:14px;background:var(--white);color:#999;font-size:6.5px;padding:2px 4px}
  .news-form b{background:var(--teal);color:var(--white);font-size:7px;font-weight:400;padding:2px 10px}
  .col-follow{flex:1}
  .socials{display:flex;gap:4px}
  .socials i{width:13px;height:13px;background:var(--teal)}
  .socials i:nth-child(2){background:#2f6fb0}
  .socials i:nth-child(3){background:#4a4a4a}
  .footer-bottom{position:absolute;left:0;right:0;bottom:0;height:16px;border-top:1px solid #2a2a2a;text-align:center;font-size:6.5px;color:#888;line-height:16px}
</style>
</head>
<body>

<div class="topbar">
  <div class="wrap">
    <span class="currency">USD $</span>
    <nav class="account"><a href="#">Login</a><a href="#" class="register">Register</a></nav>
  </div>
</div>

<header class="site-header">
  <div class="wrap">
    <div class="brand">Caldera Key</div>
    <div class="cart">
      <svg width="12" height="12" viewBox="0 0 12 12" fill="none" stroke="#fff" stroke-width="1.2">
        <path d="M1 2h2l1.3 5.5h5L11 4H4"/><circle cx="5" cy="9.8" r=".9" fill="#fff"/><circle cx="9" cy="9.8" r=".9" fill="#fff"/>
      </svg>
    </div>
    <div class="search-line"></div>
    <nav class="main-nav">
      <a href="#" class="active">Home</a><a href="#">About</a><a href="#">Service</a><a href="#">Product</a><a href="#">Contact</a>
    </nav>
  </div>
</header>

<section class="hero">
  <div class="hero-photo" role="img" aria-label="Beach scene: woman in a sun hat holding a coconut drink before a turquoise sea and white sand"></div>
  <h1 class="hero-title">“ WELCOME TO <em>Caldera Key</em> ”</h1>
  <div class="hero-dots"><span class="on"></span><span></span><span></span></div>
</section>

<section class="services">
  <div class="wrap">
    <article class="service">
      <div class="service-img" role="img" aria-label="Small bird perched on a branch in green forest" style="background:linear-gradient(160deg,#5f8a3a,#2f5a22 60%,#8fae5c)"></div>
      <h3>Selling guided tours</h3>
      <p>Duis sed odio sit amet nibh vulputate cursus a sit amet mauris. Morbi accumsan ipsum velit.</p>
      <a href="#" class="btn">Read more</a>
    </article>
    <article class="service">
      <div class="service-img" role="img" aria-label="Hotel pool with palm trees and loungers at dusk" style="background:linear-gradient(180deg,#d98a3c,#b65a2a 45%,#2e7f86 75%,#1f5e63)"></div>
      <h3>Hotel/ Hostels</h3>
      <p>Duis sed odio sit amet nibh vulputate cursus a sit amet mauris. Morbi accumsan ipsum velit.</p>
      <a href="#" class="btn">Read more</a>
    </article>
    <article class="service">
      <div class="service-img" role="img" aria-label="White tour bus on a road" style="background:linear-gradient(180deg,#a9c9e4,#e8eef2 55%,#8c8f93)"></div>
      <h3>Rental Vehicles</h3>
      <p>Duis sed odio sit amet nibh vulputate cursus a sit amet mauris. Morbi accumsan ipsum velit.</p>
      <a href="#" class="btn">Read more</a>
    </article>
  </div>
</section>

<section class="converter" role="img" aria-label="Dark blurred tropical backdrop">
  <div class="wrap">
    <div class="converter-box">
      <h2>Currency Converter</h2>
      <div class="field"><label>From</label><div class="select">US Dollar <b></b></div></div>
      <div class="field"><label>To</label><div class="select">Panama Balboa <b></b></div></div>
      <div class="field"><label>Amount</label><div class="input"></div><span class="btn btn-go">Go</span></div>
    </div>
    <div class="converter-copy">
      <h2>Currency Converter</h2>
      <p>Duis sed odio sit amet nibh vulputate cursus a sit amet mauris. Morbi accumsan ipsum velit. Nam nec tellus a odio tincidunt auctor a ornare odio. Sed non mauris vitae erat consequat auctor eu in elit.</p>
      <a href="#" class="btn">Read More</a>
    </div>
  </div>
</section>

<section class="populars">
  <div class="wrap">
    <h2>Most Populars</h2>
    <div class="pop-list">
      <article class="pop">
        <h3>Duis sed odio</h3>
        <div class="pop-img" role="img" aria-label="Wild animal on dry grassland" style="background:linear-gradient(180deg,#c8b48a,#a88a55)"></div>
        <div class="stars">★★★★★</div>
        <p>Duis sed odio sit amet nibh vulputate cursus.</p>
        <div class="pop-foot"><span class="more">Read more</span><span class="price">$79</span></div>
        <a href="#" class="btn">Read More</a>
      </article>
      <article class="pop">
        <h3>Duis sed odio</h3>
        <div class="pop-img" role="img" aria-label="Island coastline seen from above" style="background:linear-gradient(180deg,#5fb7d6,#2d8aa6 55%,#7aa35a)"></div>
        <div class="stars">★★★★★</div>
        <p>Duis sed odio sit amet nibh vulputate cursus.</p>
        <div class="pop-foot"><span class="more">Read more</span><span class="price">$79</span></div>
        <a href="#" class="btn">Read More</a>
      </article>
      <article class="pop">
        <h3>Duis sed odio</h3>
        <div class="pop-img" role="img" aria-label="Tropical beach with palms at sunset" style="background:linear-gradient(180deg,#f0b46a,#e6874a 40%,#2c8fa8 70%,#e9d7b0)"></div>
        <div class="stars">★★★★★</div>
        <p>Duis sed odio sit amet nibh vulputate cursus.</p>
        <div class="pop-foot"><span class="more">Read more</span><span class="price">$79</span></div>
        <a href="#" class="btn">Read More</a>
      </article>
      <article class="pop">
        <h3>Duis sed odio</h3>
        <div class="pop-img" role="img" aria-label="Wild animal in savanna grass" style="background:linear-gradient(180deg,#d9c9a2,#b39660)"></div>
        <div class="stars">★★★★★</div>
        <p>Duis sed odio sit amet nibh vulputate cursus.</p>
        <div class="pop-foot"><span class="more">Read more</span><span class="price">$79</span></div>
        <a href="#" class="btn">Read More</a>
      </article>
    </div>
    <div class="pager"><span>1</span><span>2</span><span>3</span></div>
  </div>
</section>

<footer class="site-footer">
  <div class="wrap footer-cols">
    <div class="col-about">
      <h4>Caldera Key</h4>
      <p>Duis sed odio sit amet nibh vulputate cursus a sit amet mauris. Morbi accumsan ipsum velit.</p>
      <a href="#" class="btn">Call to action</a>
    </div>
    <div class="col-links">
      <h4>Quick Links</h4>
      <ul><li>Home</li><li>About</li><li>Service</li><li>Product</li><li>Contact</li></ul>
    </div>
    <div class="col-news">
      <h4>Get Monthly News</h4>
      <div class="news-form"><span>Email Address</span><b>Send</b></div>
    </div>
    <div class="col-follow">
      <h4>Follow Us</h4>
      <div class="socials"><i></i><i></i><i></i><i></i></div>
    </div>
  </div>
  <div class="footer-bottom">© 2015 Caldera Key. All rights reserved.</div>
</footer>

</body>
</html>
```